Velkora Land Surveying Website Design

We are working with Velkora. They are a national land surveying company and in need of a new website design.

Some sites to use for inspiration:

https://brannickeng.com
https://www.dvwinc.com
https://kelvarin.com
https://gto.us
https://ravendobuilt.com
https://www.marbeckquillondale.com

Thank you for taking the time to consider designing a website for us. We are web developers based in Stockton and Los Angeles, CA, USA. Most of our projects go through the same process. Understanding this process may help you win a project with us. We custom-code all of our websites in-house. We don’t have any requirements as to what tools you use for your design, but we prefer Figma files. For any design that we label as four-stars, we send it to the client for review. The client picks the final design they want us to use. Once we complete this process, we will continue to show additional clients all the four-star sites and purchase them later. Your designs will have multiple chances to sell. For better chances of success, we ask that you follow these guidelines.

IMAGES:
If you use any images or icons in the design, we ask that you have a link to the asset so we can purchase the image/icon. Most of the designs we submit do not have the customer’s images on them unless they have some great images. Be creative; show us the feeling you are trying to portray with your image choices. Use any royalty-free site you choose. We subscribe to Pellix and mainly use their images, but we can purchase images outside of Pellix.

PLEASE NOTE: we will not submit designs to clients with watermarks on the images.

FONTS:
We ask that you identify the fonts used in the design. This can be done in a message if you want. We typically use Google Fonts and Pellix Fonts.

CONTENT:
We're always open to different content and ideas. We often submit designs with stock images so the client can see our vision. We typically take pictures after the website launch to use their images with our vision. Lorem Ipsum is fine for paragraphs, but we ask that you write the headers in correct English. We want to be able to show the vision and identify the sections of the website.

INSPIRATION:
We typically add a couple of links in the brief of websites we like to help you get started in your design.

REVISIONS:
We do not often ask for revisions of the designs unless we see something in the design that may not appeal to the client. If there are slight changes that we want to make, we do that in the development process.

FEEDBACK:
We rarely give feedback on designs during the design process. We are working on many website projects and do not have the time to provide feedback. We usually respond if your request is well thought out and asks specific questions, but a note asking “feedback, please” usually goes unanswered.

```html
<!DOCTYPE html>
<html lang="en">
<head>
<meta charset="utf-8">
<title>Velkora Land Surveying</title>
<link href="https://fonts.googleapis.com/css2?family=Oswald:wght@400;500;600&family=Lato:wght@400;700&family=Montserrat:wght@400;500;600;700&display=swap" rel="stylesheet">
<style>
:root{
  --red:#e02b2b;
  --red-dark:#c41f1f;
  --ink:#1c1c1c;
  --text:#3a3a3a;
  --grey:#6a6a6a;
  --grey-dark:#4a4a4a;
  --icon-grey:#5a5a5a;
  --bar:#1f1f1f;
  --white:#ffffff;
}
*{margin:0;padding:0;box-sizing:border-box}
html,body{width:1200px;height:4090px;overflow:hidden;background:var(--white)}
body{font-family:"Lato",sans-serif;color:var(--text)}
.page{position:relative;width:1200px;height:4090px;overflow:hidden}
.abs{position:absolute}
.shapes{position:absolute;left:0;top:0}
.oswald{font-family:"Oswald",sans-serif}
.btn{position:absolute;display:flex;align-items:center;justify-content:center;background:var(--red);color:var(--white);font-family:"Montserrat",sans-serif;font-weight:700;font-size:15px;border-radius:0 30px 30px 0;text-transform:uppercase;clip-path:polygon(14px 0,100% 0,100% 100%,0 100%)}
.btn.dark{background:var(--grey-dark)}
.brand{position:absolute;display:flex;align-items:center;gap:14px}
.brand .dot{width:52px;height:52px;border-radius:50%;background:var(--red)}
.brand .name{font-family:"Oswald",sans-serif;font-weight:600;font-size:40px;color:var(--red);letter-spacing:1px;line-height:1}
.topbar{position:absolute;left:486px;top:0;display:flex;gap:26px;font-family:"Montserrat",sans-serif;font-size:13px;color:var(--white);height:38px;align-items:center}
.topbar span{display:flex;align-items:center;gap:8px}
.nav{position:absolute;left:460px;top:70px;display:flex;gap:16px;font-family:"Montserrat",sans-serif;font-size:14px;color:var(--ink)}
.nav .on{color:var(--red);font-weight:600;text-decoration:underline}
.label{position:absolute;left:0;width:1200px;display:flex;justify-content:center;align-items:center;gap:12px;font-family:"Oswald",sans-serif;font-weight:500;font-size:22px;color:var(--ink);text-transform:uppercase}
.label i{width:16px;height:16px;border-radius:50%;background:var(--red);display:block}
.title{position:absolute;left:0;width:1200px;text-align:center;font-family:"Oswald",sans-serif;font-weight:500;font-size:36px;line-height:44px;color:var(--ink);text-transform:uppercase}
.hero-title{left:611px;top:212px;font-family:"Oswald",sans-serif;font-weight:500;font-size:60px;line-height:64px;color:var(--white)}
.hero-title .hl{display:inline-block;background:var(--red);padding:0 6px;line-height:62px;margin-top:2px}
.hero-text{left:616px;top:358px;width:420px;font-size:16px;line-height:25px;color:var(--white)}
.about-text{left:627px;top:906px;width:400px;font-size:13.5px;line-height:24px;text-align:justify}
.card{position:absolute;width:463px;height:136px;background:var(--white);display:flex;align-items:center;gap:20px;padding:0 20px}
.card.active{border:3px solid var(--red)}
.ico{width:92px;height:92px;border-radius:50%;border:2px dashed var(--red);display:flex;align-items:center;justify-content:center;flex:none}
.ico svg{display:block}
.card h3{font-family:"Oswald",sans-serif;font-weight:500;font-size:18px;color:var(--ink);margin-bottom:10px}
.card p{font-size:15px;line-height:23px;color:var(--ink);padding-left:4px}
.why h4{font-family:"Oswald",sans-serif;font-weight:500;font-size:17px;color:var(--ink);margin-bottom:6px;line-height:22px}
.why p{font-size:12.5px;line-height:25px;color:var(--text)}
.feat-ico{position:absolute;width:76px;height:76px;border-radius:50%;background:var(--white);box-shadow:0 4px 14px rgba(0,0,0,.15);display:flex;align-items:center;justify-content:center}
.center-mark{position:absolute;left:492px;top:2307px;width:216px;height:216px;display:flex;flex-direction:column;align-items:center;justify-content:center;gap:12px}
.center-mark .dot{width:60px;height:60px;border-radius:50%;background:var(--red)}
.center-mark .name{font-family:"Oswald",sans-serif;font-weight:600;font-size:34px;color:var(--red);letter-spacing:1px;line-height:1}
.proj-card{left:119px;top:2836px;width:320px;height:386px;border:2px solid var(--red);border-right:none;background:var(--white);padding:48px 24px}
.proj-card h3{font-family:"Oswald",sans-serif;font-weight:500;font-size:23px;color:var(--ink);margin-bottom:18px}
.proj-card p{font-size:13.5px;line-height:24px;color:var(--ink)}
.proj-img{position:absolute;top:2836px;height:386px}
.proj-img span{position:absolute;left:16px;bottom:20px;font-family:"Oswald",sans-serif;font-weight:500;font-size:18px;line-height:25px;color:var(--white)}
.contact-text{position:absolute;left:0;width:1200px;top:3522px;text-align:center;font-size:13.5px;color:var(--white)}
.foot h5{font-family:"Montserrat",sans-serif;font-weight:500;font-size:18px;color:var(--ink);margin-bottom:18px}
.foot ul{list-style:none;font-family:"Montserrat",sans-serif;font-size:14px;color:var(--ink)}
.foot li{margin-bottom:12px;display:flex;align-items:center;gap:8px}
.foot .ci{display:flex;gap:14px;align-items:flex-start;font-family:"Montserrat",sans-serif;font-size:14px;line-height:24px;color:var(--ink);margin-bottom:14px}
.foot .ci b{width:30px;height:30px;border-radius:50%;background:var(--red);flex:none;display:flex;align-items:center;justify-content:center}
.copy{position:absolute;left:0;width:1200px;top:4048px;text-align:center;font-family:"Montserrat",sans-serif;font-size:12.5px;color:var(--ink)}
</style>
</head>
<body>
<div class="page">

<svg class="shapes" width="1200" height="4090" viewBox="0 0 1200 4090">
  <defs>
    <linearGradient id="heroGrad" x1="0" y1="0" x2="0" y2="1">
      <stop offset="0" stop-color="#6f6250"/><stop offset="0.45" stop-color="#8a5a3c"/><stop offset="1" stop-color="#a8643c"/>
    </linearGradient>
    <radialGradient id="heroGlow" cx="0.78" cy="0.2" r="0.6">
      <stop offset="0" stop-color="#c9b48a" stop-opacity="0.75"/><stop offset="1" stop-color="#c9b48a" stop-opacity="0"/>
    </radialGradient>
    <radialGradient id="heroLeft" cx="0.25" cy="0.45" r="0.45">
      <stop offset="0" stop-color="#3e4a3a" stop-opacity="0.55"/><stop offset="1" stop-color="#3e4a3a" stop-opacity="0"/>
    </radialGradient>
    <linearGradient id="heroShade" x1="0" y1="0" x2="1" y2="0">
      <stop offset="0.45" stop-color="#000" stop-opacity="0"/><stop offset="1" stop-color="#000" stop-opacity="0.35"/>
    </linearGradient>
    <linearGradient id="aboutGrad" x1="0" y1="0" x2="1" y2="1">
      <stop offset="0" stop-color="#d8cfa8"/><stop offset="0.45" stop-color="#b7b85a"/><stop offset="1" stop-color="#7a6a52"/>
    </linearGradient>
    <radialGradient id="aboutGlow" cx="0.6" cy="0.4" r="0.45">
      <stop offset="0" stop-color="#d6e14a" stop-opacity="0.6"/><stop offset="1" stop-color="#d6e14a" stop-opacity="0"/>
    </radialGradient>
    <linearGradient id="servGrad" x1="0" y1="0" x2="1" y2="0">
      <stop offset="0" stop-color="#6e6a62"/><stop offset="0.5" stop-color="#676767"/><stop offset="1" stop-color="#5f6266"/>
    </linearGradient>
    <linearGradient id="redGrad" x1="0" y1="0" x2="1" y2="0">
      <stop offset="0" stop-color="#e23030"/><stop offset="0.5" stop-color="#e23a34"/><stop offset="1" stop-color="#d82626"/>
    </linearGradient>
    <radialGradient id="softFade" cx="1" cy="0.4" r="0.9">
      <stop offset="0" stop-color="#ececec"/><stop offset="1" stop-color="#fff" stop-opacity="0"/>
    </radialGradient>
  </defs>
  <polygon points="420,0 1200,0 1200,38 446,38" fill="var(--bar)"/>
  <polygon points="127,578 1073,578 1073,602 600,684 127,602" fill="var(--red)"/>
  <g role="img" aria-label="Surveyor with hard hat operating a tripod level on a construction site">
    <polygon points="0,119 1200,119 1200,560 600,656 0,560" fill="url(#heroGrad)"/>
    <polygon points="0,119 1200,119 1200,560 600,656 0,560" fill="url(#heroGlow)"/>
    <polygon points="0,119 1200,119 1200,560 600,656 0,560" fill="url(#heroLeft)"/>
    <polygon points="0,119 1200,119 1200,560 600,656 0,560" fill="url(#heroShade)"/>
  </g>
  <rect x="880" y="690" width="320" height="260" fill="url(#softFade)"/>
  <circle cx="348" cy="971" r="217" fill="var(--red)"/>
  <g role="img" aria-label="Surveyor in safety vest looking through a survey level">
    <circle cx="352" cy="984" r="208" fill="url(#aboutGrad)"/>
    <circle cx="352" cy="984" r="208" fill="url(#aboutGlow)"/>
  </g>
  <polygon points="119,1340 600,1282 1081,1340 1081,1362 119,1362" fill="var(--red)"/>
  <g role="img" aria-label="Faded survey instruments on a construction site">
    <polygon points="0,1362 119,1362 119,1352 600,1296 1081,1352 1081,1362 1200,1362 1200,1935 1081,1935 1081,1948 600,2020 119,1948 119,1935 0,1935" fill="url(#servGrad)"/>
  </g>
  <polygon points="119,1935 1081,1935 1081,1966 600,2047 119,1966" fill="var(--red)"/>
  <circle cx="600" cy="2415" r="185" fill="none" stroke="#333" stroke-width="1.5" stroke-dasharray="6 6"/>
  <circle cx="600" cy="2415" r="124" fill="#fff" stroke="#eee" stroke-width="8"/>
  <circle cx="600" cy="2415" r="108" fill="#fff" stroke="#f2f2f2" stroke-width="2"/>
  <polygon points="119,3345 600,3317 1081,3345 1081,3362 119,3362" fill="var(--grey-dark)"/>
  <g role="img" aria-label="Red tinted photo of surveyors at work">
    <polygon points="0,3362 119,3362 119,3350 600,3328 1081,3350 1081,3362 1200,3362 1200,3680 1081,3680 1081,3690 600,3712 119,3690 119,3680 0,3680" fill="url(#redGrad)"/>
  </g>
  <polygon points="119,3680 1081,3680 1081,3695 600,3722 119,3695" fill="var(--grey-dark)"/>
  <line x1="119" y1="4022" x2="1079" y2="4022" stroke="#333" stroke-width="1.5"/>
</svg>

<!-- header -->
<div class="brand" style="left:119px;top:30px">
  <div class="dot"></div>
  <div class="name">VELKORA</div>
</div>
<div class="topbar">
  <span><svg width="16" height="16" viewBox="0 0 24 24"><circle cx="12" cy="12" r="11" fill="none" stroke="#fff" stroke-width="1.5"/><path d="M8 7l2 0 1 3-1.5 1a7 7 0 0 0 3.5 3.5l1-1.5 3 1v2a1 1 0 0 1-1 1A10 10 0 0 1 7 8a1 1 0 0 1 1-1z" fill="#fff"/></svg>+1 555 014 2290</span>
  <span><svg width="16" height="16" viewBox="0 0 24 24"><circle cx="12" cy="12" r="11" fill="none" stroke="#fff" stroke-width="1.5"/><rect x="6.5" y="8" width="11" height="8" fill="none" stroke="#fff" stroke-width="1.5"/><path d="M6.5 8l5.5 4.5L17.5 8" fill="none" stroke="#fff" stroke-width="1.5"/></svg>info@velkora-survey.com</span>
  <span><svg width="16" height="16" viewBox="0 0 24 24"><circle cx="12" cy="12" r="11" fill="none" stroke="#fff" stroke-width="1.5"/><path d="M12 5a4.5 4.5 0 0 0-4.5 4.5C7.5 13 12 18 12 18s4.5-5 4.5-8.5A4.5 4.5 0 0 0 12 5z" fill="#fff"/></svg>2025 Meridian Row, Canada, K2P 0Z9</span>
</div>
<div class="nav">
  <span class="on">HOME</span><span>|</span><span>ABOUT US</span><span>|</span><span>OUR SERVICES</span><span>|</span><span>PROJECTS</span>
</div>
<div class="btn" style="left:897px;top:60px;width:182px;height:43px">Contact Us</div>

<!-- hero -->
<div class="abs hero-title">NATIONAL REACH.<br><span class="hl">LOCAL PRECISION.</span></div>
<div class="abs hero-text">Trusted land surveying and geospatial solutions — serving clients across all 50 states.</div>
<div class="btn" style="left:619px;top:432px;width:190px;height:41px">Request a Quote</div>

<!-- about -->
<div class="label" style="top:752px;left:627px;width:auto;justify-content:flex-start"><i></i>About Us</div>
<div class="abs oswald" style="left:627px;top:798px;font-weight:500;font-size:34px;line-height:44px;color:var(--ink)">SURVEYING WITH INTEGRITY.<br>DELIVERING WITH ACCURACY</div>
<div class="abs about-text">Lorem Ipsum is simply dummy text of the printing and typesetting industry. Lorem Ipsum has been the industry's standard dummy text ever since the 1500s, when an unknown printer took a galley of type and scrambled it to make a type specimen book. It has survived not only five centuries, but also the leap into electronic typesetting, remaining essentially unchanged.<br>It was popularised in the 1960s with the release of Letraset sheets containing Lorem Ipsum passages, and more recently with desktop publishing software</div>
<div class="btn" style="left:627px;top:1171px;width:190px;height:43px">Read More</div>

<!-- services -->
<div class="label" style="top:1370px;color:var(--white)"><i></i>Our Services<i></i></div>
<div class="title" style="top:1412px;color:var(--white)">Comprehensive Surveying &amp;<br>Mapping Services</div>
<div class="card active" style="left:127px;top:1539px">
  <div class="ico"><svg width="74" height="74" viewBox="0 0 74 74"><circle cx="37" cy="37" r="35" fill="var(--red)"/><rect x="24" y="20" width="26" height="34" rx="2" fill="none" stroke="#fff" stroke-width="2.5"/><path d="M29 30h16M29 37h16M29 44h10" stroke="#fff" stroke-width="2.5"/></svg></div>
  <div><h3>Boundary &amp; ALTA/NSPS Surveys</h3><p>Establishing accurate property lines and title support.</p></div>
</div>
<div class="card" style="left:608px;top:1541px">
  <div class="ico"><svg width="74" height="74" viewBox="0 0 74 74"><circle cx="37" cy="37" r="35" fill="var(--icon-grey)"/><path d="M16 50l13-18 9 11 7-8 13 15z" fill="none" stroke="#fff" stroke-width="2.5" stroke-linejoin="round"/><circle cx="48" cy="24" r="4" fill="none" stroke="#fff" stroke-width="2.5"/></svg></div>
  <div><h3>Topographic Surveys</h3><p>Detailed elevation mapping for design and planning.</p></div>
</div>
<div class="card" style="left:127px;top:1692px">
  <div class="ico"><svg width="74" height="74" viewBox="0 0 74 74"><circle cx="37" cy="37" r="35" fill="var(--icon-grey)"/><rect x="20" y="20" width="34" height="34" fill="none" stroke="#fff" stroke-width="2.5"/><path d="M20 37h18M38 20v24M38 44h16" stroke="#fff" stroke-width="2.5"/></svg></div>
  <div><h3>Construction Layout</h3><p>Reliable stakeout for efficient project execution.</p></div>
</div>
<div class="card" style="left:608px;top:1692px">
  <div class="ico"><svg width="74" height="74" viewBox="0 0 74 74"><circle cx="37" cy="37" r="35" fill="var(--icon-grey)"/><path d="M37 20l18 9-18 9-18-9z" fill="none" stroke="#fff" stroke-width="2.5" stroke-linejoin="round"/><path d="M19 37l18 9 18-9M19 45l18 9 18-9" fill="none" stroke="#fff" stroke-width="2.5" stroke-linejoin="round"/></svg></div>
  <div><h3>Drone &amp; LiDAR Mapping</h3><p>High-resolution aerial and 3D site data capture.</p></div>
</div>
<div class="btn" style="left:505px;top:1876px;width:189px;height:41px">View More</div>

<!-- why choose -->
<div class="label" style="top:2122px"><i></i>Why Choose Velkora?<i></i></div>
<div class="title" style="top:2174px;font-size:35px">Your Trusted Surveying Partner</div>
<div class="abs why" style="left:60px;top:2290px;width:337px;text-align:right"><h4>National coverage with local expertise</h4><p>Lorem Ipsum is simply dummy text of the printing<br>and typesetting industry.</p></div>
<div class="abs why" style="left:60px;top:2465px;width:315px;text-align:right"><h4>Fast turnaround &amp; responsive support</h4><p>Lorem Ipsum is simply dummy text of the printing<br>and typesetting industry.</p></div>
<div class="abs why" style="left:812px;top:2290px;width:290px"><h4>Modern, defensible deliverables (CAD, GIS, BIM)</h4><p>Lorem Ipsum is simply dummy text of the<br>printing and typesetting industry.</p></div>
<div class="abs why" style="left:810px;top:2468px;width:300px"><h4>Decades of proven industry experience</h4><p>Lorem Ipsum is simply dummy text of the<br>printing and typesetting industry.</p></div>
<div class="feat-ico" style="left:424px;top:2295px"><svg width="40" height="40" viewBox="0 0 24 24"><path d="M12 2a7 7 0 0 0-7 7c0 5 7 13 7 13s7-8 7-13a7 7 0 0 0-7-7z" fill="none" stroke="var(--red)" stroke-width="1.6"/><circle cx="12" cy="9" r="2.5" fill="none" stroke="var(--red)" stroke-width="1.6"/></svg></div>
<div class="feat-ico" style="left:400px;top:2466px"><svg width="40" height="40" viewBox="0 0 24 24"><path d="M4 20h16" stroke="var(--red)" stroke-width="1.6"/><rect x="5" y="13" width="3" height="7" fill="none" stroke="var(--red)" stroke-width="1.6"/><rect x="10.5" y="9" width="3" height="11" fill="none" stroke="var(--red)" stroke-width="1.6"/><rect x="16" y="5" width="3" height="15" fill="none" stroke="var(--red)" stroke-width="1.6"/></svg></div>
<div class="feat-ico" style="left:713px;top:2295px"><svg width="40" height="40" viewBox="0 0 24 24"><rect x="4" y="3" width="16" height="18" rx="1.5" fill="none" stroke="var(--red)" stroke-width="1.6"/><path d="M7.5 8h9M7.5 12h9M7.5 16h5" stroke="var(--red)" stroke-width="1.6"/></svg></div>
<div class="feat-ico" style="left:722px;top:2477px"><svg width="40" height="40" viewBox="0 0 24 24"><path d="M12 3l2.6 5.6 6 .7-4.5 4.1 1.2 6L12 16.4 6.7 19.4l1.2-6L3.4 9.3l6-.7z" fill="none" stroke="var(--red)" stroke-width="1.6" stroke-linejoin="round"/></svg></div>
<div class="center-mark"><div class="dot"></div><div class="name">VELKORA</div></div>

<!-- projects -->
<div class="label" style="top:2666px"><i></i>Our Projects<i></i></div>
<div class="title" style="top:2708px">Surveying With Integrity.<br>Delivering With Accuracy</div>
<div class="abs proj-card">
  <h3>Interstate Bridge Expansion</h3>
  <p>Lorem Ipsum is simply dummy text of the printing and typesetting industry. Lorem Ipsum has been the industry's standard dummy text ever since the 1500s, when an unknown printer took a galley of type and scrambled it to make a type specimen book.</p>
</div>
<div class="btn" style="left:146px;top:3132px;width:190px;height:43px">View More</div>
<div class="proj-img" role="img" aria-label="Workers in hard hats beneath a bridge under construction" style="left:428px;width:297px;background:linear-gradient(180deg,#8fb4cf,#9aa7ad 35%,#7b7467 60%,#5a5246)"></div>
<div class="proj-img" role="img" aria-label="Aerial view of residential land with a location pin" style="left:736px;width:165px;background:linear-gradient(180deg,#a8bcc9,#8aa36a 35%,#6f8a52 55%,#5a4a38)"><span>Residential<br>Masterplan, Texas</span></div>
<div class="proj-img" role="img" aria-label="Rows of solar panels in a green field" style="left:912px;width:166px;background:linear-gradient(180deg,#7d8f9c,#3e4d62 45%,#4c6a3a)"><span>Solar Field,<br>California</span></div>

<!-- contact band -->
<div class="label" style="top:3412px;color:var(--white)"><i style="background:#fff"></i>Contact Us<i style="background:#fff"></i></div>
<div class="title" style="top:3462px;color:var(--white);font-size:34px">Let's Get Your Project Started</div>
<div class="contact-text">Tell us about your project's scope, location, and timeline — and our team will respond within one business day</div>
<div class="btn dark" style="left:508px;top:3574px;width:187px;height:41px">Contact Us</div>

<!-- footer -->
<div class="brand" style="left:119px;top:3790px">
  <div class="dot"></div>
  <div class="name">VELKORA</div>
</div>
<div class="abs foot" style="left:373px;top:3780px">
  <h5>MAIN LINKS</h5>
  <ul>
    <li>➜ Home</li><li>➜ About Us</li><li>➜ Services</li><li>➜ Projects</li><li>➜ Contact Us</li>
  </ul>
</div>
<div class="abs foot" style="left:603px;top:3780px">
  <h5>CONTACT US</h5>
  <div class="ci"><b><svg width="14" height="14" viewBox="0 0 24 24"><path d="M6 3l4 0 1.5 5-2.5 1.5a11 11 0 0 0 5.5 5.5l1.5-2.5 5 1.5v4a2 2 0 0 1-2 2A17 17 0 0 1 4 5a2 2 0 0 1 2-2z" fill="#fff"/></svg></b>+1 555 014 2290</div>
  <div class="ci"><b><svg width="14" height="14" viewBox="0 0 24 24"><rect x="3" y="6" width="18" height="12" fill="#fff"/><path d="M3 6l9 7 9-7" fill="none" stroke="#e02b2b" stroke-width="2"/></svg></b>info@velkora-survey.com</div>
  <div class="ci"><b><svg width="14" height="14" viewBox="0 0 24 24"><path d="M12 2a7 7 0 0 0-7 7c0 5 7 13 7 13s7-8 7-13a7 7 0 0 0-7-7z" fill="#fff"/><circle cx="12" cy="9" r="2.5" fill="#e02b2b"/></svg></b>2025 Meridian Row,<br>Canada, K2P 0Z9</div>
</div>
<div class="abs foot" style="left:862px;top:3780px;width:230px">
  <h5>NEWSLETTER SIGN UP</h5>
  <p style="font-family:Montserrat,sans-serif;font-size:12px;line-height:22px;color:var(--ink)">We Will Notify You Of Any<br>Important News</p>
  <div style="margin-top:20px;display:flex;align-items:center;width:200px;height:42px;border:1px solid #ddd;border-radius:4px;padding-left:10px;font-family:Montserrat,sans-serif;font-size:12px;color:#444;position:relative">Your Email Address
    <span style="position:absolute;right:-12px;top:-1px;width:44px;height:42px;background:var(--red);border-radius:6px;display:flex;align-items:center;justify-content:center"><svg width="20" height="20" viewBox="0 0 24 24"><path d="M3 11l18-8-7 18-3-7z" fill="none" stroke="#fff" stroke-width="1.8" stroke-linejoin="round"/><path d="M11 14l10-11" stroke="#fff" stroke-width="1.8"/></svg></span>
  </div>
</div>
<div class="copy">© 2025 Velkora Land Surveying | All Rights Reserved</div>

</div>
</body>
</html>
```